Yard sign

Looking for a yard sign. <br/>Something simple, name, number. <br/>Large text, readable from 50 feet away. <br/><br/>18 x 24 inches.

Target Market(s)

Potential homeowners thinking about going solar.

Colors

Designer to choose colors to be used in the design.

Requirements
Must have
• "WE'VE GONE SOLAR!"
Nice to have
• We are a solar company, we would like a design that compliments the homeowners decision that they went solar and encourages others to do the same.

```html
<!DOCTYPE html>
<html lang="en">
<head>
<meta charset="utf-8">
<title>Brightacre Solar Yard Sign</title>
<link rel="stylesheet" href="https://fonts.googleapis.com/css2?family=Roboto:wght@700&family=Roboto+Condensed:wght@700&display=swap">
<style>
  :root {
    --page: #e6e6e6;
    --sign-white: #ffffff;
    --brand-orange: #f58f22;
    --sun-yellow: #fcc62b;
    --band-red: #dc440a;
    --ink: #111111;
  }
  html, body {
    margin: 0;
    width: 1200px;
    height: 1200px;
    overflow: hidden;
    background: var(--page);
  }
  .sign {
    position: absolute;
    left: 0;
    top: 150px;
    width: 1200px;
    height: 900px;
    background: var(--sign-white);
    overflow: hidden;
  }
  .brand-mark {
    position: absolute;
    left: 190px;
    top: 110px;
    width: 200px;
    height: 200px;
    border-radius: 50%;
    background: var(--sun-yellow);
  }
  .brand-name {
    position: absolute;
    left: 430px;
    top: 128px;
    margin: 0;
    font-family: "Roboto", Arial, sans-serif;
    font-weight: 700;
    color: var(--brand-orange);
    line-height: 1;
  }
  .brand-name .word-main {
    display: block;
    font-size: 100px;
    letter-spacing: -2px;
  }
  .brand-name .word-sub {
    display: block;
    margin-top: 16px;
    font-size: 44px;
    letter-spacing: 14px;
  }
  .headline {
    position: absolute;
    left: 0;
    width: 1200px;
    top: 410px;
    margin: 0;
    text-align: center;
    font-family: "Roboto", Arial, sans-serif;
    font-weight: 700;
    font-size: 68px;
    line-height: 1;
    color: var(--brand-orange);
  }
  .rule {
    position: absolute;
    top: 625px;
    height: 9px;
    background: var(--band-red);
  }
  .rule-left { left: 0; width: 356px; }
  .rule-right { left: 845px; width: 355px; }
  .rep-name {
    position: absolute;
    left: 0;
    width: 1200px;
    top: 566px;
    margin: 0;
    text-align: center;
    font-family: "Roboto Condensed", "Arial Narrow", sans-serif;
    font-weight: 700;
    font-size: 76px;
    letter-spacing: -1px;
    line-height: 1;
    color: var(--band-red);
  }
  .contact-band {
    position: absolute;
    left: 0;
    top: 646px;
    width: 1200px;
    height: 254px;
    background: var(--band-red);
    text-align: center;
  }
  .phone {
    display: block;
    margin-top: 24px;
    font-family: "Roboto", Arial, sans-serif;
    font-weight: 700;
    font-size: 124px;
    line-height: 1;
    color: var(--sun-yellow);
  }
  .website {
    display: block;
    margin-top: 18px;
    font-family: "Roboto", Arial, sans-serif;
    font-weight: 700;
    font-size: 50px;
    line-height: 1;
    color: var(--ink);
  }
</style>
</head>
<body>
  <main class="sign">
    <div class="brand-mark" aria-hidden="true"></div>
    <h1 class="brand-name">
      <span class="word-main">BRIGHTACRE</span>
      <span class="word-sub">SOLAR</span>
    </h1>

    <h2 class="headline">WE'VE GONE SOLAR!</h2>

    <div class="rule rule-left"></div>
    <p class="rep-name">MARCUS BELL</p>
    <div class="rule rule-right"></div>

    <section class="contact-band">
      <span class="phone">555-014-2867</span>
      <span class="website">www.brightacre-solar.net</span>
    </section>
  </main>
</body>
</html>
```